kolvarin.link kolvarin.space kolvarin.press website

The website is named KOLVARIN and it will have 3 domain names. kolvarin.link, press, space.
I'd like it to be viewed on Pads, pcs and phones.

page menu:

kolvarin.link(start page): presentation of company. (creative, design, app, new product innovation.)
Here we'll need sosial media icons: plimber, vendoloop, mirtavel, trelvanet. (light but some 'fruity' colors)

kolvarin.press: blog. It will be a 75% picture blog > rest will be text. I need to be able to resize pictures and shape columns to picture size. (light but some 'fruity' colors)

kolvarin.space : the fun part of this web design, however, on entering the page I'd like a non-disclosure agreement where viewer simply click "yes, I agree" after filling out contact info. (check attached document)
We will have space here for uploading PDF files viewers can download. There is also a blog space here to tell in brief about the PDF file. (maybe a space/sci-fi theme her e.g spacechimp, Laika the space dog?)

I will attach the logo here I want you to use > and develop for the .space .press webpage. The logo i uploaded is for the .link page.

Target Market(s)

venture capitalists

Number of Pages Required

3 page

Requirements
Must have
• a few 'fruity colors' but mostly white and grey

```html
<!DOCTYPE html>
<html lang="en">
<head>
<meta charset="utf-8">
<title>KOLVARIN LINK</title>
<link href="https://fonts.googleapis.com/css2?family=Silkscreen:wght@400;700&family=Open+Sans:ital,wght@0,400;0,600;0,700;1,400&display=swap" rel="stylesheet">
<style>
:root{
  --green:#4aab4c;
  --leaf:#7cb342;
  --orange:#ff6a0e;
  --teal:#1dbc9c;
  --red:#e5473a;
  --purple:#6a4d8d;
  --blue:#1f8bc6;
  --tangerine:#f26a21;
  --ink:#222222;
  --text:#777777;
  --hero:#f1f6f9;
  --light:#f0f0f0;
  --dark:#232323;
  --darker:#1a1a1a;
  --white:#ffffff;
}
*{box-sizing:border-box;margin:0;padding:0}
html,body{width:1200px;height:2568px;overflow:hidden}
body{font-family:"Open Sans",Arial,sans-serif;color:var(--text);background:var(--white);position:relative}
.pixel{font-family:"Silkscreen","Courier New",monospace;text-transform:uppercase}
.abs{position:absolute}

/* header */
.site-header{position:absolute;left:0;top:0;width:1200px;height:137px}
.brand{left:99px;top:38px;display:flex;align-items:center;gap:12px;font-family:"Silkscreen",monospace;font-weight:700;font-size:38px;color:var(--ink);line-height:1}
.brand-mark{width:26px;height:26px;background:var(--orange)}
.social{right:99px;top:40px;display:flex;align-items:center;gap:14px}
.social-label{font-size:11px;color:var(--ink);margin-right:4px}
.social-item{width:42px;height:42px;border-radius:6px;box-shadow:3px 3px 0 #333}
.s-mirtavel{background:#2f74c0}.s-plimber{background:#e53b3b}.s-vendoloop{background:#6b3f8e}.s-trelvanet{background:#f39a16}

/* nav */
.main-nav{left:99px;top:137px;width:1002px;height:51px;background:var(--green);display:flex;align-items:center;justify-content:space-between;padding:0 30px 0 28px;z-index:2}
.main-nav::before,.main-nav::after{content:"";position:absolute;top:22px;width:7px;height:7px;border-radius:50%;background:var(--ink)}
.main-nav::before{left:8px}.main-nav::after{right:8px}
.main-nav a{color:var(--white);text-decoration:none;font-size:13px;font-weight:700;display:flex;align-items:center;gap:10px}
.main-nav a.active{color:var(--red)}
.nav-dot{width:24px;height:24px;background:var(--red);border-radius:4px}

/* hero */
.hero{left:0;top:137px;width:1200px;height:522px;background:var(--hero)}
.hero-art{left:40px;top:105px;width:695px;height:340px;border-radius:14px;background:linear-gradient(135deg,#5c6a7c 0%,#7b8fa3 45%,#3d8f94 100%);opacity:.85}
.hero-copy{left:792px;top:165px;width:310px}
.hero-title{font-size:36px;font-weight:700;color:var(--ink);letter-spacing:1px;line-height:1}
.hero-text{margin-top:22px;color:var(--red);font-size:14px;font-weight:600;line-height:24px}
.btn{display:inline-block;color:var(--white);font-family:"Silkscreen",monospace;font-size:11px;text-transform:uppercase;padding:0 20px;height:42px;line-height:42px;box-shadow:0 3px 0 rgba(0,0,0,.25)}
.btn-red{background:var(--red)}.btn-green{background:var(--green)}
.hero-copy .btn{margin-top:25px;width:146px;text-align:center;padding:0}
.dots{display:flex;gap:10px;margin-top:26px}
.dots span{width:16px;height:16px;border-radius:50%;border:2px solid #888}
.dots span.on{background:var(--green);border-color:var(--green)}

/* section heads */
.section-head{left:0;width:1200px;text-align:center}
.section-head h2{font-family:"Silkscreen",monospace;font-weight:700;font-size:25px;color:var(--ink);letter-spacing:1px}
.section-head p{width:840px;margin:8px auto 0;font-size:13px;line-height:21px}

/* services */
.services{left:99px;top:797px;width:1002px;display:flex;justify-content:space-between}
.service{width:231px;height:281px;color:var(--white);text-align:center;padding-top:20px;box-shadow:0 3px 0 rgba(0,0,0,.2)}
.service .icon{width:102px;height:102px;border-radius:50%;background:var(--white);margin:0 auto;display:flex;align-items:center;justify-content:center}
.service h3{font-family:"Silkscreen",monospace;font-size:14px;font-weight:400;margin-top:28px;letter-spacing:1px}
.service p{font-size:11px;line-height:19px;margin:7px 16px 0}
.service .chev{margin-top:8px}
.sv-leaf{background:var(--leaf)}.sv-orange{background:var(--orange)}.sv-teal{background:var(--teal)}.sv-red{background:var(--red)}

/* welcome */
.welcome{left:0;top:1127px;width:1200px;height:288px;background:linear-gradient(180deg,#1c1c1c,#262626 50%,#1c1c1c);text-align:center;color:var(--white)}
.welcome h2{font-family:"Silkscreen",monospace;font-weight:700;font-size:26px;margin-top:52px;letter-spacing:1px}
.welcome p{width:1010px;margin:12px auto 0;font-size:12px;line-height:24px}
.welcome .actions{margin-top:24px;display:flex;justify-content:center;gap:9px}
.welcome .btn{height:41px;line-height:41px;padding:0;width:145px}

/* news */
.news-phone{left:523px;top:1565px;width:155px;height:330px;border-radius:26px;background:linear-gradient(160deg,#e6f2f8,#c9dce6);border:3px solid #b7cfdc}
.news-phone .screen{position:absolute;left:10px;top:52px;width:129px;height:220px;background:linear-gradient(160deg,#e8b35a,#d0614f 50%,#8a6a9a)}
.news-item{width:300px}
.news-item h4{font-family:"Silkscreen",monospace;font-size:13px;color:var(--ink);font-weight:400}
.news-item p{font-size:11px;line-height:19px;margin-top:10px}
.news-item .date{font-family:"Silkscreen",monospace;font-size:10px;color:var(--green);margin-top:8px}
.news-left{text-align:right}
.connector{height:1px;background:#d5dde2}
.connector::after{content:"";position:absolute;top:-4px;width:7px;height:7px;border:1px solid #c5cfd5;border-radius:50%;background:var(--white)}
.c-left::after{left:-8px}.c-right::after{right:-8px}

/* testimonials */
.testimonials{left:0;top:1945px;width:1200px;height:342px;background:var(--light)}
.quote{width:313px;height:150px;color:var(--white);font-size:11px;line-height:20px;padding:16px 22px 0 22px;position:relative}
.quote::after{content:"";position:absolute;right:22px;bottom:-16px;border-top:16px solid;border-left:16px solid transparent;border-top-color:inherit}
.quote .mark{position:absolute;font-size:22px;font-weight:700;line-height:1}
.q-open{left:12px;top:10px}.q-close{right:16px;bottom:10px}
.q-purple{background:var(--purple);border-color:var(--purple)}
.q-blue{background:var(--blue);border-color:var(--blue)}
.q-orange{background:var(--tangerine);border-color:var(--tangerine)}
.quote-name{font-style:italic;font-size:14px;color:var(--ink);text-align:right;margin-top:26px;padding-right:10px}

/* footer */
.site-footer{left:0;top:2287px;width:1200px;height:216px;background:var(--dark);color:#c8c8c8;font-size:12px}
.site-footer h5{font-family:"Silkscreen",monospace;color:var(--white);font-size:14px;font-weight:400;letter-spacing:1px}
.f-menu{left:99px;top:24px}
.f-menu li{list-style:none;line-height:22px;margin-top:0}
.f-menu ul{margin-top:12px}
.f-contact{left:236px;top:24px;width:230px}
.f-contact .addr{margin-top:12px;line-height:21px}
.f-line{display:flex;align-items:center;gap:14px;margin-top:14px}
.f-line.big{font-size:15px}
.f-tweets{left:520px;top:24px;width:230px}
.tweet{display:flex;gap:12px;margin-top:14px;line-height:21px;font-size:11px}
.tweet i{flex:none;width:15px;height:15px;background:#e8e8e8;margin-top:3px}
.f-news{left:835px;top:30px;width:266px}
.f-news p{font-size:11px;line-height:20px;margin-top:12px}
.subscribe{display:flex;margin-top:18px;height:39px}
.subscribe span{flex:1;background:#1b1b1b;color:#888;font-size:11px;line-height:39px;padding-left:12px}
.subscribe b{width:80px;background:var(--red);color:var(--white);font-family:"Silkscreen",monospace;font-weight:400;font-size:11px;text-align:center;line-height:39px}
.bottom-bar{left:0;top:2503px;width:1200px;height:65px;background:var(--darker);color:#ddd;font-size:11px;text-align:center;line-height:65px}
</style>
</head>
<body>

<header class="site-header">
  <div class="abs brand"><span class="brand-mark"></span>KOLVARIN</div>
  <div class="abs social">
    <span class="social-label pixel">Our social networks:</span>
    <span class="social-item s-mirtavel" role="img" aria-label="mirtavel"></span>
    <span class="social-item s-plimber" role="img" aria-label="plimber"></span>
    <span class="social-item s-vendoloop" role="img" aria-label="vendoloop"></span>
    <span class="social-item s-trelvanet" role="img" aria-label="trelvanet"></span>
  </div>
</header>

<section class="abs hero">
  <div class="abs hero-art" role="img" aria-label="Illustration of a desktop monitor showing fruit app icons, with stacked coding books, an apple and a pencil"></div>
  <div class="abs hero-copy">
    <h1 class="hero-title pixel">KOLVARIN LINK</h1>
    <p class="hero-text">Accusantium doloremque laudantium, totam rem aperiam, eaque ipsa quae ab illo...</p>
    <a class="btn btn-red">Read more info</a>
    <div class="dots"><span class="on"></span><span></span><span></span></div>
  </div>
</section>

<nav class="abs main-nav pixel">
  <a class="active"><span class="nav-dot"></span>Home</a>
  <a>About</a><a>Services</a><a>Features</a><a>Testimonials</a><a>News</a><a>Contact</a>
</nav>

<div class="abs section-head" style="top:690px">
  <h2>Our Services</h2>
  <p>Sed ut perspiciatis unde omnis iste natus error sit voluptatem accusantium doloremque laudantium, totam rem aperiam, eaque ipsa quae ab illo inventore veritatis et quasi architecto beatae vitae dicta sunt explicabo.</p>
</div>

<section class="abs services">
  <article class="service sv-leaf">
    <div class="icon"><svg width="44" height="36" viewBox="0 0 44 36" fill="none" stroke="#7cb342" stroke-width="3"><rect x="2" y="2" width="40" height="32"/><polyline points="6,30 17,17 25,25 31,19 38,30" fill="#7cb342"/><circle cx="31" cy="10" r="3" fill="#7cb342"/></svg></div>
    <h3>Creative Design</h3>
    <p>Accusantium doloremquetium, totam rem aperiam, eaque ipsa quae ab illo inventore veritatis et...</p>
    <svg class="chev" width="18" height="16" viewBox="0 0 18 16" fill="none" stroke="#fff" stroke-width="2.5"><polyline points="2,2 9,8 16,2"/><polyline points="2,8 9,14 16,8"/></svg>
  </article>
  <article class="service sv-orange">
    <div class="icon"><svg width="46" height="32" viewBox="0 0 46 32" fill="none" stroke="#ff6a0e" stroke-width="3"><rect x="7" y="3" width="32" height="21"/><line x1="2" y1="28" x2="44" y2="28"/></svg></div>
    <h3>App Creation</h3>
    <p>Accusantium doloremquetium, totam rem aperiam, eaque ipsa quae ab illo inventore veritatis et...</p>
    <svg class="chev" width="18" height="16" viewBox="0 0 18 16" fill="none" stroke="#fff" stroke-width="2.5"><polyline points="2,2 9,8 16,2"/><polyline points="2,8 9,14 16,8"/></svg>
  </article>
  <article class="service sv-teal">
    <div class="icon"><svg width="42" height="42" viewBox="0 0 42 42" fill="none" stroke="#1dbc9c" stroke-width="3" stroke-linejoin="round"><polygon points="21,3 38,12 38,31 21,40 4,31 4,12"/><polyline points="4,12 21,21 38,12"/><line x1="21" y1="21" x2="21" y2="40"/></svg></div>
    <h3>New Product</h3>
    <p>Accusantium doloremquetium, totam rem aperiam, eaque ipsa quae ab illo inventore veritatis et...</p>
    <svg class="chev" width="18" height="16" viewBox="0 0 18 16" fill="none" stroke="#fff" stroke-width="2.5"><polyline points="2,2 9,8 16,2"/><polyline points="2,8 9,14 16,8"/></svg>
  </article>
  <article class="service sv-red">
    <div class="icon"><svg width="44" height="40" viewBox="0 0 44 40" fill="#e5473a"><circle cx="16" cy="22" r="11"/><circle cx="16" cy="22" r="4" fill="#fff"/><g stroke="#e5473a" stroke-width="5"><line x1="16" y1="7" x2="16" y2="37"/><line x1="1" y1="22" x2="31" y2="22"/><line x1="5" y1="11" x2="27" y2="33"/><line x1="27" y1="11" x2="5" y2="33"/></g><circle cx="16" cy="22" r="4" fill="#fff"/><circle cx="34" cy="10" r="7"/><circle cx="34" cy="10" r="2.5" fill="#fff"/></svg></div>
    <h3>Other Service</h3>
    <p>Accusantium doloremquetium, totam rem aperiam, eaque ipsa quae ab illo inventore veritatis et...</p>
    <svg class="chev" width="18" height="16" viewBox="0 0 18 16" fill="none" stroke="#fff" stroke-width="2.5"><polyline points="2,2 9,8 16,2"/><polyline points="2,8 9,14 16,8"/></svg>
  </article>
</section>

<section class="abs welcome">
  <h2>Welcome to Kolvarin Link</h2>
  <p>Sed ut perspiciatis unde omnis iste natus error sit voluptatem accusantium doloremque laudantium, totam rem aperiam, eaque ipsa quae ab illo inventore veritatis et quasi architecto beatae vitae dicta sunt explicabo. Nemo enim ipsam voluptatem quia voluptas sit aspernatur aut odit aut fugit, sed quia consequuntur magni dolores eos qui ratione voluptatem sequi nesciunt.Neque porro quisquam est, qui dolorem ipsum...</p>
  <div class="actions"><a class="btn btn-red">Read more info</a><a class="btn btn-green">Get start today</a></div>
</section>

<div class="abs section-head" style="top:1448px">
  <h2>Recent News Articles</h2>
  <p>Sed ut perspiciatis unde omnis iste natus error sit voluptatem accusantium doloremque laudantium, totam rem aperiam, eaque ipsa quae ab illo inventore veritatis et quasi architecto beatae vitae dicta sunt explicabo.</p>
</div>

<div class="abs news-phone"><div class="screen" role="img" aria-label="Phone screen showing colourful fruit app icons"></div></div>
<div class="abs connector c-left" style="left:428px;top:1605px;width:95px"></div>
<div class="abs connector c-right" style="left:678px;top:1605px;width:95px"></div>
<div class="abs connector c-left" style="left:428px;top:1762px;width:95px"></div>
<div class="abs connector c-right" style="left:678px;top:1762px;width:95px"></div>

<article class="abs news-item news-left" style="left:100px;top:1597px">
  <h4>Totam rem aperiam</h4>
  <p>Sed ut perspiciatis unde omnis iste natus error sit tatem doloremque laudantium, totam rem aperiam, eaque ipsa quae ab illoNeque porro inventore veritatis et quasi...</p>
  <div class="date">Posted on 22 , March , 2016</div>
</article>
<article class="abs news-item" style="left:800px;top:1597px">
  <h4>Totam rem aperiam</h4>
  <p>Sed ut perspiciatis unde omnis iste natus error sit tatem doloremque laudantium, totam rem aperiam, eaque ipsa quae ab illoNeque porro inventore veritatis et quasi...</p>
  <div class="date">Posted on 24 , March , 2016</div>
</article>
<article class="abs news-item news-left" style="left:100px;top:1754px">
  <h4>Totam rem aperiam</h4>
  <p>Sed ut perspiciatis unde omnis iste natus error sit tatem doloremque laudantium, totam rem aperiam, eaque ipsa quae ab illoNeque porro inventore veritatis et quasi...</p>
  <div class="date">Posted on 22 , March , 2016</div>
</article>
<article class="abs news-item" style="left:800px;top:1754px">
  <h4>Totam rem aperiam</h4>
  <p>Sed ut perspiciatis unde omnis iste natus error sit tatem doloremque laudantium, totam rem aperiam, eaque ipsa quae ab illoNeque porro inventore veritatis et quasi...</p>
  <div class="date">Posted on 24 , March , 2016</div>
</article>

<section class="abs testimonials">
  <div class="abs section-head" style="top:42px"><h2>What people say about us?</h2></div>
  <div class="abs" style="left:99px;top:102px">
    <blockquote class="quote q-purple"><span class="mark q-open">“</span>Lorem ipsum dolor sit amet, consectetur adipi-scing elit, sed do eiusmod tempor incididunt ut labore et dolore magna aliqua. Ut enim ad minim veniam, quis nostrud exeation ullamco laboris nisi ut Lorem ipsum dolor sit amet.<span class="mark q-close">”</span></blockquote>
    <div class="quote-name">Mara Velt</div>
  </div>
  <div class="abs" style="left:443px;top:102px">
    <blockquote class="quote q-blue"><span class="mark q-open">“</span>Lorem ipsum dolor sit amet, consectetur adipi-scing elit, sed do eiusmod tempor incididunt ut labore et dolore magna aliqua. Ut enim ad minim veniam, quis nostrud exeation ullamco laboris nisi ut Lorem ipsum dolor sit amet.<span class="mark q-close">”</span></blockquote>
    <div class="quote-name">Odrin Kessa</div>
  </div>
  <div class="abs" style="left:788px;top:102px">
    <blockquote class="quote q-orange"><span class="mark q-open">“</span>Lorem ipsum dolor sit amet, consectetur adipi-scing elit, sed do eiusmod tempor incididunt ut labore et dolore magna aliqua. Ut enim ad minim veniam, quis nostrud exeation ullamco laboris nisi ut Lorem ipsum dolor sit amet.<span class="mark q-close">”</span></blockquote>
    <div class="quote-name">Tavi Rendlow</div>
  </div>
</section>

<footer class="abs site-footer">
  <div class="abs f-menu">
    <h5>Menu</h5>
    <ul><li>Home</li><li>About</li><li>Service</li><li>Features</li><li>News</li><li>Contact</li></ul>
  </div>
  <div class="abs f-contact">
    <h5>Contact us</h5>
    <p class="addr">1609 Kolvarin Studio name,<br>Street name,City name-4664</p>
    <div class="f-line big"><svg width="18" height="18" viewBox="0 0 24 24" fill="none" stroke="#c8c8c8" stroke-width="2"><path d="M5 3h4l2 5-3 2a12 12 0 0 0 6 6l2-3 5 2v4a2 2 0 0 1-2 2A17 17 0 0 1 3 5a2 2 0 0 1 2-2z"/></svg>(+120) 555-0147</div>
    <div class="f-line"><svg width="18" height="14" viewBox="0 0 18 14" fill="none" stroke="#c8c8c8" stroke-width="1.6"><rect x="1" y="1" width="16" height="12"/><polyline points="1,1 9,8 17,1"/></svg>info@kolvarin.link</div>
  </div>
  <div class="abs f-tweets">
    <h5>Latest Tweet`s</h5>
    <div class="tweet"><i></i><span>Good morning .... wherever you are today! All of us at ...See more here kolvarin.link/notes</span></div>
    <div class="tweet"><i></i><span>Good morning .... wherever you are today! All of us at ...See more here kolvarin.link/notes</span></div>
  </div>
  <div class="abs f-news">
    <h5>Newsletter</h5>
    <p>Excepteur sint occaecat cupidatat non proident, sunt in culpa qui officia deserunt mollit anim</p>
    <div class="subscribe"><span>Enter your email address</span><b>Sign up</b></div>
  </div>
</footer>
<div class="abs bottom-bar">© 2016 KOLVARIN LINK - ALL RIGHTS RESERVED</div>

</body>
</html>
```